Upmarket Dessert Lounge needs a Business Card Design

We are an upmarket dessert lounge needing a business card to match our image.

We want something that is simple yet beautiful, feminine, classy, sophisticated and elegant. We want it to stand out and don't mind if it is bold.

The design should include our logo and colours of red or maroon with gold highlights. We don't mind if black is used.

Marlow & Quince

Target Market(s)

For those who like to indulge or treat themselves and give in to their temptations on good quality desserts.

Industry/Entity Type

Business

Requirements
Must have
• Must include our logo and our name

Marlow & Quince

M & Q

```html
<!DOCTYPE html>
<html lang="en">
<head>
<meta charset="utf-8">
<title>Marlow &amp; Quince — Business Card</title>
<link rel="stylesheet" href="https://fonts.googleapis.com/css2?family=Open+Sans:wght@400;700&display=swap">
<style>
  :root {
    --backdrop: #d9d9d9;
    --card-black: #000000;
    --maroon: #7a1416;
    --gold: #f0c27c;
    --cream: #f7dba4;
    --white: #ffffff;
  }
  * { margin: 0; padding: 0; box-sizing: border-box; }
  html, body {
    width: 956px;
    height: 1200px;
    overflow: hidden;
    background: var(--backdrop);
    font-family: "Open Sans", Arial, sans-serif;
  }
  .canvas { position: relative; width: 956px; height: 1200px; }
  .card {
    position: absolute;
    width: 798px;
    height: 455px;
    background: var(--card-black);
    border-radius: 28px;
    overflow: hidden;
  }
  .card--front { left: 78px; top: 96px; }
  .card--back { left: 74px; top: 632px; }
  .card__swoosh { position: absolute; inset: 0; }

  .brand-name {
    position: absolute;
    color: var(--cream);
    font-weight: 400;
    white-space: nowrap;
    transform: translate(-50%, -50%);
    letter-spacing: 1px;
  }
  .brand-name--front { left: 245px; top: 139px; font-size: 32px; }
  .brand-name--back { left: 398px; top: 228px; font-size: 78px; }

  .holder { position: absolute; left: 60px; top: 278px; color: var(--gold); }
  .holder__name { font-size: 20px; font-weight: 700; line-height: 30px; }
  .holder__role { font-size: 20px; font-weight: 400; line-height: 30px; }

  .contact {
    position: absolute;
    color: var(--white);
    font-size: 18px;
    line-height: 27px;
    list-style: none;
  }
  .contact__key { font-weight: 700; }
  .contact--phones { left: 64px; top: 354px; }
  .contact--web { left: 277px; top: 310px; }
  .contact--address { left: 279px; top: 380px; }
</style>
</head>
<body>
<main class="canvas">
  <section class="card card--front" aria-label="Business card front">
    <svg class="card__swoosh" width="798" height="455" viewBox="0 0 798 455" aria-hidden="true">
      <path d="M552 0 C690 60 760 250 670 455 L798 455 L798 0 Z" fill="var(--maroon)"/>
      <path d="M652 0 C740 95 765 300 692 455 L712 455 C775 300 760 110 690 0 Z" fill="var(--card-black)"/>
    </svg>
    <p class="brand-name brand-name--front">MARLOW &amp; QUINCE</p>
    <div class="holder">
      <p class="holder__name">Your Name</p>
      <p class="holder__role">Designation</p>
    </div>
    <ul class="contact contact--phones">
      <li><span class="contact__key">p</span> : 123-456-7890</li>
      <li><span class="contact__key">c</span> : 123-456-7890</li>
      <li><span class="contact__key">f</span> : 123-456-7890</li>
    </ul>
    <ul class="contact contact--web">
      <li><span class="contact__key">e</span> : name@yourwebsite.com</li>
      <li><span class="contact__key">w</span> : www.marlow&amp;quince.com</li>
    </ul>
    <address class="contact contact--address" style="font-style:normal">
      0000, Street Name<br>
      City Name, Country Code.
    </address>
  </section>

  <section class="card card--back" aria-label="Business card back">
    <p class="brand-name brand-name--back">M &amp; Q</p>
  </section>
</main>
</body>
</html>
```